Business card for my new company (Accounting firm)

I need a business card for my new business Brightwell Advisory and Ledger SA. Our services are accounting, tax, audit and financial management. Our customers are small companies, start-ups and new companies. The final design has to show financial security, trust and growth. Please find our logo attached to the business card. Text for the business card: Brightwell Advisory and Ledger SA Tomas Varenholt Director and Founder Certified Accountant Tel. 022 418 57 34 tv@clairevalconseil.ch www.clairevalconseil.ch Rue des Vergières 27 1201 Geneva
Target Market(s)
Our customers are small companies, start-ups and new companies.
Industry/Entity Type
Finance And Accounting
Contact Information for Business Card
Claireval Conseil et Comptes SA
Tomas Varenholt
Directeur et Fondateur
Expert-comptable diplômé
Tél. 022 418 57 34
tv@clairevalconseil.ch
www.clairevalconseil.ch
Rue des Vergières 27
1201 Genève

```html
<!DOCTYPE html>
<html lang="fr">
<head>
<meta charset="utf-8">
<title>Claireval Conseil et Comptes SA – Carte de visite</title>
<link href="https://fonts.googleapis.com/css2?family=Roboto:wght@400;500;700&display=swap" rel="stylesheet">
<style>
  :root {
    --page-bg: #d9dadb;
    --card-front: #ffffff;
    --card-back: #f4f5f6;
    --ink-dark: #3a3d40;
    --ink-mid: #4a4d50;
    --brand-blue: #1f5f93;
    --brand-blue-light: #2c9ad6;
    --brand-blue-mid: #1f7fc0;
  }
  * { box-sizing: border-box; margin: 0; padding: 0; }
  html, body { width: 1200px; height: 726px; overflow: hidden; }
  body {
    background: var(--page-bg);
    font-family: "Roboto", Arial, sans-serif;
    position: relative;
  }
  .card {
    position: absolute;
    width: 540px;
    height: 318px;
    top: 204px;
    border-radius: 3px;
    box-shadow: 0 6px 18px rgba(0,0,0,0.12);
    overflow: hidden;
  }
  .card--front { left: 40px; background: var(--card-front); }
  .card--back { left: 620px; background: var(--card-back); }

  .wordmark {
    display: flex;
    align-items: center;
    gap: 10px;
    font-weight: 500;
    color: var(--ink-dark);
    white-space: nowrap;
  }
  .wordmark__square {
    width: 22px; height: 22px;
    background: var(--brand-blue-mid);
    flex: none;
  }
  .card--front .wordmark {
    position: absolute;
    left: 0; right: 0; top: 118px;
    justify-content: center;
    font-size: 27px;
  }
  .front-stripe {
    position: absolute;
    left: 0; right: 0; top: 252px;
  }
  .front-stripe__light { height: 3px; background: var(--brand-blue-light); }
  .front-stripe__dark { height: 6px; background: var(--brand-blue); }

  .card--back .wordmark {
    position: absolute;
    right: 28px; top: 112px;
    font-size: 19px;
  }
  .card--back .wordmark__square { width: 18px; height: 18px; }

  .contact {
    position: absolute;
    left: 34px; top: 92px;
    color: var(--ink-mid);
  }
  .contact__name {
    font-size: 21px;
    font-weight: 700;
    color: var(--brand-blue);
    margin-bottom: 4px;
  }
  .contact__role { font-size: 13px; line-height: 17px; }
  .contact__address { margin-top: 44px; font-size: 14px; line-height: 19px; }
  .contact__list { list-style: none; margin-top: 8px; font-size: 14px; line-height: 20px; }
  .contact__list li { display: flex; align-items: center; gap: 12px; }
  .contact__icon { width: 13px; height: 13px; flex: none; fill: var(--brand-blue); }
</style>
</head>
<body>
  <section class="card card--front" aria-label="Recto">
    <div class="wordmark"><span class="wordmark__square"></span>Claireval Conseil et Comptes</div>
    <div class="front-stripe">
      <div class="front-stripe__light"></div>
      <div class="front-stripe__dark"></div>
    </div>
  </section>

  <section class="card card--back" aria-label="Verso">
    <div class="contact">
      <h1 class="contact__name">Tomas Varenholt</h1>
      <p class="contact__role">Directeur et Fondateur</p>
      <p class="contact__role">Expert-comptable diplômé</p>
      <address class="contact__address" style="font-style:normal">
        Rue des Vergières 27<br>1201 Genève
      </address>
      <ul class="contact__list">
        <li>
          <svg class="contact__icon" viewBox="0 0 16 16" aria-hidden="true"><path d="M3 1h3l1.5 4-2 1.3a9 9 0 0 0 4.2 4.2L11 8.5l4 1.5v3a2 2 0 0 1-2 2A12 12 0 0 1 1 3a2 2 0 0 1 2-2z"/></svg>
          022 418 57 34
        </li>
        <li>
          <svg class="contact__icon" viewBox="0 0 16 16" aria-hidden="true"><path d="M1 3h14v10H1z M2 4l6 5 6-5" stroke="#f4f5f6" stroke-width="1"/></svg>
          tv@clairevalconseil.ch
        </li>
        <li>
          <svg class="contact__icon" viewBox="0 0 16 16" aria-hidden="true"><circle cx="8" cy="8" r="7"/><path d="M1 8h14M8 1c-3 3-3 11 0 14M8 1c3 3 3 11 0 14" stroke="#f4f5f6" stroke-width="1" fill="none"/></svg>
          www.clairevalconseil.ch
        </li>
      </ul>
    </div>
    <div class="wordmark"><span class="wordmark__square"></span>Claireval Conseil et Comptes</div>
  </section>
</body>
</html>
```